QVR business card

Need a business card for a company that provides instructional design and elearning development services. The website is here: http://quorvane.studio/

I'm attaching a current logo, as well as the old business card design. While I like to keep it clean, the old design is too simplistic for my liking. The only idea I want to reuse from the old design is placing industry jargon on the back of the card, just need a better way to present it. But if you have other ideas for the back--feel free to experiment.

Please use the colors complementary to the color we have on the website. Thank you!

```html
<!DOCTYPE html>
<html lang="en">
<head>
<meta charset="utf-8">
<title>QVR business card</title>
<link rel="stylesheet" href="https://fonts.googleapis.com/css2?family=Nunito:wght@700;800&family=PT+Sans:wght@400;700&display=swap">
<style>
  :root {
    --stage: #a9a9a9;
    --card-front-a: #ffffff;
    --card-front-b: #e4e4e4;
    --teal: #2aa39a;
    --teal-light: #38b5ae;
    --teal-dark: #14928a;
    --gold: #c9bb86;
    --ink: #3f3f3f;
    --ink-soft: #4d4d4d;
  }
  * { box-sizing: border-box; margin: 0; padding: 0; }
  html, body { width: 1200px; height: 900px; overflow: hidden; }
  body {
    background: var(--stage);
    font-family: "PT Sans", Arial, sans-serif;
    position: relative;
  }
  .card {
    position: absolute;
    top: 295px;
    width: 540px;
    height: 310px;
    box-shadow: 0 6px 18px rgba(0,0,0,.3);
    overflow: hidden;
  }
  /* Front */
  .card-front {
    left: 40px;
    background: linear-gradient(100deg, var(--card-front-a) 0%, var(--card-front-a) 25%, var(--card-front-b) 60%, var(--card-front-a) 100%);
  }
  .brand {
    font-family: "Nunito", Arial, sans-serif;
    font-weight: 800;
    letter-spacing: 2px;
  }
  .card-front .brand {
    position: absolute;
    left: 36px;
    top: 30px;
    font-size: 58px;
    line-height: 1;
    color: var(--teal);
  }
  .holder {
    position: absolute;
    right: 32px;
    top: 150px;
    text-align: right;
  }
  .holder-name {
    font-family: "Nunito", Arial, sans-serif;
    font-weight: 800;
    font-size: 21px;
    margin-bottom: 10px;
  }
  .holder-name .first { color: var(--teal); }
  .holder-name .last { color: var(--gold); }
  .contact-list { list-style: none; }
  .contact-list li {
    display: flex;
    justify-content: flex-end;
    align-items: center;
    gap: 7px;
    font-size: 14px;
    color: var(--ink);
    height: 25px;
    letter-spacing: .3px;
  }
  .contact-list svg { width: 15px; height: 15px; fill: none; stroke: var(--teal); stroke-width: 1.6; }
  .contact-list .icon-fill { fill: var(--teal); stroke: none; }

  /* Back */
  .card-back {
    left: 620px;
    background: linear-gradient(90deg, var(--teal-light) 0%, var(--teal-dark) 100%);
  }
  .card-back .brand {
    position: absolute;
    left: 0; right: 0;
    top: 28px;
    text-align: center;
    font-size: 54px;
    line-height: 1;
    color: var(--gold);
  }
  .rule {
    position: absolute;
    height: 3px;
    background: var(--ink-soft);
  }
  .rule-left { left: 0; top: 128px; width: 130px; }
  .rule-right { right: 0; top: 178px; width: 260px; }
  .help-title {
    position: absolute;
    left: 145px;
    top: 115px;
    font-size: 22px;
    font-weight: 400;
    color: var(--ink-soft);
    letter-spacing: 1px;
  }
  .services {
    position: absolute;
    list-style: none;
    color: var(--ink-soft);
    font-size: 14px;
    letter-spacing: 1.2px;
    text-transform: uppercase;
    line-height: 22px;
  }
  .services li { word-spacing: 10px; }
  .services-left { left: 30px; top: 158px; }
  .services-right { right: 28px; top: 200px; text-align: left; }
</style>
</head>
<body>

<section class="card card-front" aria-label="Card front">
  <div class="brand">QVR</div>
  <div class="holder">
    <p class="holder-name"><span class="first">Marlo</span> <span class="last">Vennick</span></p>
    <ul class="contact-list">
      <li>555-014-2287
        <svg viewBox="0 0 16 16" aria-hidden="true"><path class="icon-fill" d="M3 5c0-2 2-3 5-3s5 1 5 3v1h-3V5H6v1H3zM4 8l2-2h4l2 2v5H4z"/></svg>
      </li>
      <li>mvennick@quorvane.studio
        <svg viewBox="0 0 16 16" aria-hidden="true"><rect x="1.5" y="3.5" width="13" height="9"/><path d="M1.5 3.5l6.5 5 6.5-5"/></svg>
      </li>
      <li>www.quorvane.studio
        <svg viewBox="0 0 16 16" aria-hidden="true"><circle cx="8" cy="8" r="6.5"/><ellipse cx="8" cy="8" rx="2.8" ry="6.5"/><path d="M1.5 8h13"/></svg>
      </li>
    </ul>
  </div>
</section>

<section class="card card-back" aria-label="Card back">
  <div class="brand">QVR</div>
  <span class="rule rule-left"></span>
  <h2 class="help-title">HOW CAN WE HELP?</h2>
  <span class="rule rule-right"></span>
  <ul class="services services-left">
    <li>Mobile Learning SCORM</li>
    <li>Instructional Design LMS</li>
    <li>MOOCs eLearning HTML5</li>
  </ul>
  <ul class="services services-right">
    <li>Adult Learning Theory</li>
    <li>Gamification Classroom</li>
    <li>xAPI Blended Learning</li>
  </ul>
</section>

</body>
</html>
```